Fern Acupuncture Business Card Design

I would like a business card design for my acupuncture business which is based from 2 practices in Melbourne, Australia.

The front of the card should include:

*The Logo
* Name - Miranda Tesselhoff (B.App.Sc.(TCM), Dip.Rem.Mass.). (I would like the letters after my name in slightly smaller font)
* Mobile number - 0472 318 604
* Web address - www.fernacupuncture.com.au

On the back of the card I would somehow like to fit my 2 clinic addresses in. They are:

The Calm & Balance Rooms
842 Pellam St, Camberwell VIC 3124
Ph: 1300 287 419

Riverbend Natural Therapies & Herbal Practice
19 Quillon Ave, Malvern East VIC 3145
Ph: (03) 9731 4052

If there is space, I'd also like to add to the back of the card - Next Appointment............................ (or something along those lines).

Thanks and happy designing!

Target Market(s)

Health consumers, and colleagues in the health industry

Industry/Entity Type

Clinic

Contact Information for Business Card

as above in brief

Requirements
Must have
• I've seen some ok designs coming in, however I'd like to avoid the generic look with the added curved line details etc. I don't particularly need extra patterns added to the card. I'd prefer it to look quite clean and simple, and using more earthy colours (I'm not super keen on the lime green that a lot of designs seem to include. I don't mind the full black or white look, (obviously the back side needs to be a lighter colour to allow me to write appointment details on it). I also quite like the idea of the background looking like brown recycled paper (just an idea - that's not 100% necessary).
Nice to have
• I have an idea that I could have the main flower part of the logo printed as metallic.
Should not have
• Generic patterns and too much added detail.

```html
<!DOCTYPE html>
<html lang="en">
<head>
<meta charset="utf-8">
<title>Fern Acupuncture Business Card</title>
<link rel="stylesheet" href="https://fonts.googleapis.com/css2?family=Archivo:wght@400;700;800&display=swap">
<style>
  :root {
    --page-bg: #d9d9d6;
    --cream-light: #fbfde8;
    --cream: #f6f1b4;
    --gold-light: #f3ecb0;
    --gold: #e6d67e;
    --earth-deep: #b89a4e;
    --earth-olive: #a8a060;
    --ink: #141414;
    --band: #0d0d0d;
    --paper-white: #ffffff;
  }
  * { margin: 0; padding: 0; box-sizing: border-box; }
  html, body {
    width: 1200px; height: 960px; overflow: hidden;
    background: var(--page-bg);
    font-family: "Archivo", Arial, sans-serif;
    color: var(--ink);
  }
  .sheet {
    width: 1200px; height: 960px;
    display: flex; flex-direction: column; align-items: center; justify-content: center;
    gap: 60px;
  }
  .card {
    position: relative;
    width: 700px; height: 400px;
    border-radius: 16px;
    overflow: hidden;
    box-shadow: 0 6px 18px rgba(0,0,0,0.18);
  }

  /* Front */
  .card-front {
    background: linear-gradient(160deg, var(--cream-light) 0%, var(--cream) 100%);
  }
  .brand {
    position: absolute; top: 34px; left: 0; right: 0;
    display: flex; flex-direction: column; align-items: center; gap: 10px;
  }
  .brand-mark {
    width: 92px; height: 92px; border-radius: 50%;
    background: var(--band);
  }
  .brand-name {
    font-weight: 700; font-size: 15px; letter-spacing: 0.06em;
    color: var(--ink);
  }
  .practitioner {
    position: absolute; top: 182px; left: 0; right: 0; text-align: center;
  }
  .practitioner-name { font-weight: 800; font-size: 30px; line-height: 1.1; }
  .practitioner-quals { font-weight: 700; font-size: 13px; margin-top: 4px; }
  .contact {
    position: absolute; top: 262px; left: 0; right: 0; text-align: center;
    font-weight: 700; font-size: 17px; line-height: 1.6;
  }
  .front-rule {
    position: absolute; left: 0; right: 0; bottom: 40px; height: 2px; background: var(--band);
  }
  .front-band {
    position: absolute; left: 0; right: 0; bottom: 0; height: 34px; background: var(--band);
  }

  /* Back */
  .card-back {
    background: linear-gradient(150deg, var(--cream-light) 0%, var(--gold-light) 55%, var(--gold) 100%);
  }
  .back-decoration {
    position: absolute; top: -60px; right: 60px;
    width: 280px; height: 190px;
    border-radius: 0 0 140px 140px;
    background: radial-gradient(ellipse at 50% 20%, var(--earth-deep) 0%, var(--earth-olive) 35%, rgba(230,214,126,0) 80%);
    opacity: 0.55;
  }
  .clinics {
    position: absolute; left: 34px; top: 100px;
  }
  .clinic + .clinic { margin-top: 14px; }
  .clinic-name { font-weight: 800; font-size: 17px; line-height: 1.25; }
  .clinic-line { font-size: 14px; line-height: 1.35; display: flex; align-items: center; gap: 6px; }
  .clinic-line svg { width: 12px; height: 12px; flex: none; }
  .appointment {
    position: absolute; left: 250px; right: 18px; bottom: 18px; height: 130px;
    background: var(--paper-white);
    padding: 18px 24px 0 24px;
    font-size: 17px;
  }
  .appointment-title { font-size: 19px; margin-bottom: 12px; }
  .appointment-row { display: flex; align-items: baseline; gap: 6px; margin-bottom: 14px; }
  .dots { flex: 1; border-bottom: 2px dotted var(--ink); transform: translateY(-4px); }
</style>
</head>
<body>
<main class="sheet">

  <section class="card card-front" aria-label="Business card front">
    <div class="brand">
      <span class="brand-mark"></span>
      <span class="brand-name">Fern Acupuncture</span>
    </div>
    <div class="practitioner">
      <p class="practitioner-name">Miranda Tesselhoff</p>
      <p class="practitioner-quals">(B.App.Sc.(TCM), Dip.Rem.Mass.)</p>
    </div>
    <div class="contact">
      <p>0472 318 604</p>
      <p>www.fernacupuncture.com.au</p>
    </div>
    <div class="front-rule"></div>
    <div class="front-band"></div>
  </section>

  <section class="card card-back" aria-label="Business card back">
    <div class="back-decoration" role="img" aria-label="Soft enlarged petal decoration in earthy gold tones"></div>

    <div class="clinics">
      <div class="clinic">
        <p class="clinic-name">The Calm &amp; Balance Rooms</p>
        <p class="clinic-line">842 Pellam St, Camberwell VIC 3124</p>
        <p class="clinic-line">
          <svg viewBox="0 0 24 24" aria-hidden="true"><path fill="#141414" d="M6.6 10.8a15.1 15.1 0 0 0 6.6 6.6l2.2-2.2a1 1 0 0 1 1-.25 11.4 11.4 0 0 0 3.6.6 1 1 0 0 1 1 1V20a1 1 0 0 1-1 1A17 17 0 0 1 3 4a1 1 0 0 1 1-1h3.5a1 1 0 0 1 1 1c0 1.25.2 2.45.6 3.6a1 1 0 0 1-.25 1z"/></svg>
          1300 287 419
        </p>
      </div>
      <div class="clinic">
        <p class="clinic-name">Riverbend Natural Therapies &amp; Herbal Practice</p>
        <p class="clinic-line">19 Quillon Ave, Malvern East VIC 3145</p>
        <p class="clinic-line">
          <svg viewBox="0 0 24 24" aria-hidden="true"><path fill="#141414" d="M6.6 10.8a15.1 15.1 0 0 0 6.6 6.6l2.2-2.2a1 1 0 0 1 1-.25 11.4 11.4 0 0 0 3.6.6 1 1 0 0 1 1 1V20a1 1 0 0 1-1 1A17 17 0 0 1 3 4a1 1 0 0 1 1-1h3.5a1 1 0 0 1 1 1c0 1.25.2 2.45.6 3.6a1 1 0 0 1-.25 1z"/></svg>
          (03) 9731 4052
        </p>
      </div>
    </div>

    <div class="appointment">
      <p class="appointment-title">Next Appointment</p>
      <div class="appointment-row"><span>Date</span><span class="dots"></span><span>Time</span><span class="dots"></span></div>
      <div class="appointment-row"><span>Date</span><span class="dots"></span><span>Time</span><span class="dots"></span></div>
    </div>
  </section>

</main>
</body>
</html>
```